Business Card Design

New business card design

Target Market(s)

Residential & Commercial Property Managers

Industry/Entity Type

Plumbing Services

Contact Information for Business Card

Name - Rowan Keddle, title - Director, Phone Number - 0431 286 517, email - rowan@tbk-plumbing.com.au, Company ABN - 73 215 904 386,

Font styles to use
Sans Serif

Colors
0054AA
0677BA
7BADD7
CADEEF
E8F1F8

```html
<!DOCTYPE html>
<html lang="en">
<head>
<meta charset="utf-8">
<title>TBK Plumbing Services – Business Card</title>
<link href="https://fonts.googleapis.com/css2?family=Montserrat:wght@400;600&display=swap" rel="stylesheet">
<style>
  :root {
    --stage: #1b1c1e;
    --card-light: #f3f3f3;
    --card-dark: #1d232a;
    --ink: #1f262d;
    --ink-light: #f4f4f4;
    --accent: #2aa3dc;
  }
  * { box-sizing: border-box; margin: 0; padding: 0; }
  html, body { width: 1200px; height: 1059px; overflow: hidden; }
  body {
    background: var(--stage);
    font-family: "Montserrat", sans-serif;
    position: relative;
  }
  .card {
    position: absolute;
    left: 256px;
    width: 690px;
    height: 392px;
    border-radius: 18px;
  }
  .card--front { top: 89px; background: var(--card-light); color: var(--ink); }
  .card--back { top: 547px; background: var(--card-dark); color: var(--ink-light); }

  .brand {
    position: absolute;
    left: 0; right: 0;
    display: flex;
    align-items: center;
    justify-content: center;
    gap: 14px;
    font-weight: 400;
    font-size: 34px;
    letter-spacing: 0.04em;
  }
  .card--front .brand { top: 98px; color: var(--ink); }
  .card--back .brand { top: 168px; color: var(--ink-light); }
  .brand__dot {
    width: 16px; height: 16px;
    border-radius: 50%;
    background: var(--accent);
    flex: none;
  }

  .person {
    position: absolute;
    right: 374px;
    top: 252px;
    text-align: right;
  }
  .person__name {
    color: var(--accent);
    font-weight: 600;
    font-size: 28px;
    line-height: 1;
  }
  .person__title {
    font-size: 18px;
    margin-top: 6px;
    line-height: 1;
  }
  .divider {
    position: absolute;
    left: 343px;
    top: 244px;
    width: 1.5px;
    height: 73px;
    background: var(--accent);
  }
  .contact {
    position: absolute;
    left: 366px;
    top: 240px;
    font-size: 17.5px;
    line-height: 1;
  }
  .contact__row { display: flex; align-items: center; gap: 8px; white-space: nowrap; }
  .contact__row + .contact__row { margin-top: 14px; }
  .contact__row--abn { margin-bottom: 6px; padding-left: 0; }
  .contact__label { color: var(--accent); }
  .contact__icon { width: 13px; height: 13px; flex: none; }
</style>
</head>
<body>
  <section class="card card--front" aria-label="Business card front">
    <div class="brand"><span class="brand__dot"></span><span>tbk plumbing services</span></div>

    <div class="person">
      <p class="person__name">Rowan Keddle</p>
      <p class="person__title">Director</p>
    </div>

    <div class="divider"></div>

    <div class="contact">
      <p class="contact__row contact__row--abn"><span class="contact__label">ABN</span> - 73 215 904 386</p>
      <p class="contact__row">
        <svg class="contact__icon" viewBox="0 0 24 24" aria-hidden="true"><path fill="#2aa3dc" d="M6.6 10.8c1.4 2.8 3.8 5.1 6.6 6.6l2.2-2.2c.3-.3.7-.4 1-.2 1.1.4 2.3.6 3.6.6.6 0 1 .4 1 1V20c0 .6-.4 1-1 1C10.6 21 3 13.4 3 4c0-.6.4-1 1-1h3.5c.6 0 1 .4 1 1 0 1.2.2 2.4.6 3.6.1.3 0 .7-.2 1L6.6 10.8z"/></svg>
        <span>0431 286 517</span>
      </p>
      <p class="contact__row">
        <svg class="contact__icon" viewBox="0 0 24 24" aria-hidden="true"><rect x="2" y="5" width="20" height="14" fill="#2aa3dc"/><path d="M2 5l10 8 10-8M2 19l7-6M22 19l-7-6" stroke="#f3f3f3" stroke-width="1.6" fill="none"/></svg>
        <span>rowan@tbk-plumbing.com.au</span>
      </p>
    </div>
  </section>

  <section class="card card--back" aria-label="Business card back">
    <div class="brand"><span class="brand__dot"></span><span>tbk plumbing services</span></div>
  </section>
</body>
</html>
```